Commercial Swimming Pool - Design-Build Contractor Website Design

I need a new website that will feature our newly developed logo and trade name as well as provide a fully updated site experience. We are not a residential builder - we strictly design and install high-end commercial pools. I need the website to highlight our portfolio and communicate the various types of projects in which we specialize. I want the effect of the site to reflect the high-end nature of our services - projects like the 57th floor spa at the Phila Silver Willow, the aquatic therapy portion of the Phila Ravenhawks training facility, a 5om indoor competition pool for the prestigious Dallowmere Academy, the indoor water park at The Quenwick Lodge or the recent country club renovation projects we've completed in our region (to name a few examples).
Need extra days to review

```html
<!DOCTYPE html>
<html lang="en">
<head>
<meta charset="utf-8">
<title>Larkfield Aquatics — Commercial Pools</title>
<link href="https://fonts.googleapis.com/css2?family=Poppins:ital,wght@0,300;0,400;0,500;0,600;1,300;1,400&family=Montserrat:wght@800;900&family=Questrial&display=swap" rel="stylesheet">
<style>
:root{
  --navy:#1b2a55;
  --navy-deep:#15224a;
  --blue:#3aa6dd;
  --blue-light:#7cc6ec;
  --ink:#1d2333;
  --grey:#6d7280;
  --white:#ffffff;
}
*{margin:0;padding:0;box-sizing:border-box}
html,body{width:1200px;height:4478px;overflow:hidden;background:var(--white)}
body{position:relative;font-family:"Poppins",sans-serif;color:var(--ink)}
.abs{position:absolute}
.photo{position:absolute}

/* header */
.site-header{position:absolute;left:0;top:0;width:1200px;height:75px;background:var(--navy);z-index:5}
.header-curve{position:absolute;left:0;top:60px;z-index:4}
.brand{position:absolute;left:60px;top:12px;z-index:6;display:flex;align-items:center;gap:10px}
.brand-dot{width:40px;height:40px;border-radius:50%;background:var(--blue)}
.brand-name{font-family:"Poppins",sans-serif;font-weight:500;font-size:26px;line-height:1;color:var(--blue);letter-spacing:1px}
.brand-name small{display:block;font-size:8px;letter-spacing:1px;margin-top:4px;color:var(--blue)}
.nav{position:absolute;left:422px;top:30px;display:flex;gap:22px;font-size:12px;color:var(--white);z-index:6}
.nav .active{color:var(--blue);position:relative}
.nav .active::after{content:"";position:absolute;left:50%;top:20px;width:4px;height:4px;margin-left:-2px;border-radius:50%;background:var(--blue)}
.call{position:absolute;left:848px;top:17px;display:flex;gap:8px;align-items:center;z-index:6}
.call span{display:block;font-size:10px;color:var(--blue)}
.call b{display:block;font-size:16px;font-weight:400;color:var(--white);letter-spacing:.5px}
.btn-quote{position:absolute;left:1005px;top:18px;width:135px;height:37px;border-radius:6px;background:var(--blue);color:var(--white);font-size:14px;line-height:37px;text-align:center;z-index:6}

/* hero */
.hero-photo{left:0;top:0;width:1200px;height:713px;background:linear-gradient(160deg,#8ec8e6 0%,#4aa9dc 35%,#1f86c9 70%,#2d9ad6 100%)}
.hero-title{position:absolute;left:760px;top:276px;font-family:"Montserrat",sans-serif;font-weight:900;font-size:50px;line-height:58px;color:var(--white);text-transform:uppercase;letter-spacing:1px}
.btn-dark{position:absolute;left:763px;top:522px;width:150px;height:40px;border-radius:8px;background:var(--navy-deep);color:var(--white);font-size:16px;line-height:40px;text-align:center}
.slider-arrow{position:absolute;top:375px;width:38px;height:38px;background:var(--navy);display:flex;align-items:center;justify-content:center}

/* about */
.eyebrow{position:absolute;font-size:12px;color:var(--blue);letter-spacing:1px;display:flex;align-items:center;gap:10px}
.about-title{position:absolute;left:232px;top:815px;font-size:33px;line-height:42px;font-weight:400;color:var(--ink)}
.plus-link{position:absolute;display:flex;align-items:center;gap:14px;font-size:11px;color:var(--ink);letter-spacing:.5px}
.plus{width:36px;height:36px;border-radius:50%;background:var(--blue);position:relative}
.plus::before,.plus::after{content:"";position:absolute;left:50%;top:50%;background:var(--white)}
.plus::before{width:16px;height:1.5px;margin:-.75px 0 0 -8px}
.plus::after{width:1.5px;height:16px;margin:-8px 0 0 -.75px}
.about-copy{position:absolute;left:563px;top:780px;width:470px;font-style:italic;font-weight:300;font-size:12px;line-height:24px;color:var(--grey)}
.about-copy p+p{margin-top:16px}

/* services gallery */
.svc-num{position:absolute;font-family:"Poppins",sans-serif;font-weight:300;font-size:92px;line-height:1;color:transparent;-webkit-text-stroke:1.5px rgba(255,255,255,.75)}
.svc-title{position:absolute;left:267px;top:1387px;font-size:22px;color:var(--white);letter-spacing:.5px}
.svc-copy{position:absolute;left:267px;top:1424px;width:450px;font-style:italic;font-weight:300;font-size:12px;line-height:23px;color:var(--white)}

/* portfolio */
.marquee{position:absolute;left:0;top:1563px;width:1200px;height:80px;overflow:hidden;white-space:nowrap;font-family:"Poppins",sans-serif;font-weight:500;font-size:62px;line-height:80px}
.marquee span{position:absolute;top:0}
.marquee .fade{color:var(--blue-light)}
.marquee .main{color:var(--blue)}
.project-title{position:absolute;font-family:"Questrial",sans-serif;font-size:31px;line-height:44px;color:var(--ink)}

/* cta */
.cta{position:absolute;left:0;top:3428px;width:1200px;height:322px;background:var(--navy)}
.cta-photo{left:0;top:3428px;width:720px;height:322px;background:linear-gradient(90deg,#2b6fb0 0%,#2a5c9a 55%,rgba(27,42,85,1) 100%)}
.cta-title{position:absolute;left:728px;top:3495px;font-size:29px;line-height:41px;font-weight:500;text-transform:uppercase}
.cta-title .hl{color:var(--blue)}
.cta-title .wh{color:var(--white)}
.btn-blue{position:absolute;left:730px;top:3637px;width:150px;height:40px;border-radius:6px;background:var(--blue);color:var(--white);font-size:16px;line-height:40px;text-align:center;box-shadow:0 0 0 2px rgba(255,255,255,.15)}

/* testimonials */
.testi-title{position:absolute;left:125px;top:3862px;font-size:32px;font-weight:500;color:var(--ink)}
.avatar{left:130px;top:3926px;width:106px;height:106px;border-radius:50%;background:linear-gradient(135deg,#caa58e,#6e5a55);border:4px solid var(--white);box-shadow:0 0 0 1px #b8c3d3}
.quote{position:absolute;left:268px;top:3930px;width:650px;font-size:13px;line-height:26px;color:var(--grey)}
.client{position:absolute;left:272px;top:4058px;font-family:"Questrial",sans-serif;font-size:17px;color:var(--ink)}
.testi-bar{position:absolute;left:988px;width:2px;background:var(--blue)}

/* footer */
.footer{position:absolute;left:0;top:4160px;width:1200px;height:318px;background:var(--navy)}
.footer-line{position:absolute;left:0;top:4160px;width:690px;height:4px;background:var(--blue)}
.f-brand{position:absolute;left:60px;top:4210px;display:flex;align-items:center;gap:10px}
.f-about{position:absolute;left:60px;top:4310px;width:250px;font-size:11px;line-height:21px;color:var(--white)}
.social{position:absolute;top:4367px;width:38px;height:38px;border-radius:50%;border:1.5px solid var(--blue)}
.f-head{position:absolute;top:4210px;font-size:15px;font-weight:500;color:var(--white);letter-spacing:.5px}
.f-item{position:absolute;font-size:12px;line-height:20px;color:var(--white)}
.f-item .hl{color:var(--blue)}
.links{position:absolute;left:612px;top:4248px;list-style:none}
.links li{font-size:12px;color:var(--white);height:30px;padding-left:28px;position:relative}
.links li::before{content:"";position:absolute;left:3px;top:7px;width:5px;height:5px;border-radius:50%;background:var(--blue)}
.email-field{position:absolute;left:888px;top:4260px;width:255px;height:36px;border-bottom:1px solid rgba(255,255,255,.4);font-size:11px;color:var(--white);line-height:36px;padding-left:6px}
.btn-sub{position:absolute;left:888px;top:4308px;width:118px;height:38px;border-radius:6px;background:var(--blue);color:var(--white);font-size:15px;line-height:38px;text-align:center}
.copyright{position:absolute;left:0;top:4446px;width:1200px;text-align:center;font-size:11px;color:var(--white)}
.copyright .hl{color:var(--blue)}
</style>
</head>
<body>

<!-- header -->
<svg class="header-curve" width="380" height="30" viewBox="0 0 380 30" aria-hidden="true"><path d="M0 0H380C330 10 250 26 140 26C80 26 30 20 0 14Z" fill="#1b2a55"/></svg>
<header class="site-header"></header>
<div class="brand">
  <div class="brand-dot"></div>
  <div class="brand-name">LARKFIELD<small>AQUATICS · DESIGN | CONSTRUCTION</small></div>
</div>
<nav class="nav">
  <span class="active">HOME</span><span>ABOUT US</span><span>SERVICES</span><span>PROJECTS</span><span>CONTACT US</span>
</nav>
<div class="call">
  <svg width="26" height="26" viewBox="0 0 24 24" aria-hidden="true"><path d="M6.6 10.8a15 15 0 006.6 6.6l2.2-2.2c.3-.3.7-.4 1-.2 1.1.4 2.3.6 3.6.6.6 0 1 .4 1 1V20c0 .6-.4 1-1 1C10.6 21 3 13.4 3 4c0-.6.4-1 1-1h3.5c.6 0 1 .4 1 1 0 1.3.2 2.5.6 3.6.1.3 0 .7-.2 1z" fill="#3aa6dd"/></svg>
  <div><span>Call Us On :</span><b>123 456 7890</b></div>
</div>
<div class="btn-quote">GET A QUOTE</div>

<!-- hero -->
<div class="photo hero-photo" role="img" aria-label="Children swimming in a glass-walled rooftop pool overlooking a city"></div>
<h1 class="hero-title">Install<br>High-End<br>Commercial<br>Pools</h1>
<div class="btn-dark">CONTACT US</div>
<div class="slider-arrow" style="left:0"><svg width="12" height="14" viewBox="0 0 12 14"><path d="M8 2L3 7l5 5" stroke="#fff" stroke-width="1.6" fill="none"/></svg></div>
<div class="slider-arrow" style="left:1162px"><svg width="12" height="14" viewBox="0 0 12 14"><path d="M4 2l5 5-5 5" stroke="#fff" stroke-width="1.6" fill="none"/></svg></div>

<!-- about -->
<div class="eyebrow" style="left:232px;top:786px"><svg width="12" height="10" viewBox="0 0 12 10"><path d="M0 0l12 5-12 5 3-5z" fill="#3aa6dd"/></svg>ABOUT US</div>
<h2 class="about-title">LARKFIELD<br>AQUATICS</h2>
<div class="plus-link" style="left:234px;top:925px"><div class="plus"></div>LEARN MORE</div>
<div class="about-copy">
  <p>Lorem ipsum has been the industry's standard dummy text ever since the 1500s, when an unknown printer took a galley of type and scrambled it to make a type specimen book. It has survived not only.</p>
  <p>Lorem ipsum has been the industry's standard dummy text ever since the 1500s, when an unknown printer took a galley of type and scrambled it to make a type specimen book. It has survived not only five centuries, but also the leap into electronic typesetting, remaining essentially unchanged. It was popularised in the with the release.</p>
</div>

<!-- services -->
<div class="photo" style="left:232px;top:1066px;width:533px;height:424px;background:linear-gradient(180deg,#c9ced4 0%,#9ea7b0 55%,#5a6f78 100%)" role="img" aria-label="Rooftop pool beside a glass high-rise facade"></div>
<div class="photo" style="left:765px;top:1066px;width:217px;height:424px;background:linear-gradient(180deg,#3c6c96 0%,#1e4f86 50%,#1a4a8a 100%)" role="img" aria-label="Indoor pool with loungers under large windows"></div>
<div class="photo" style="left:982px;top:1066px;width:218px;height:424px;background:linear-gradient(180deg,#3a5678 0%,#264c86 50%,#2d5aa0 100%)" role="img" aria-label="Indoor lap pool with lane ropes"></div>
<div class="svc-num" style="left:228px;top:1298px">01</div>
<div class="svc-num" style="left:762px;top:1400px">02</div>
<div class="svc-num" style="left:980px;top:1400px">03</div>
<div class="svc-title">SWIMMING POOL DESIGNS</div>
<div class="svc-copy">Lorem ipsum has been the industry's standard dummy text ever since the 1500s, when an unknown printer took a galley of</div>

<!-- portfolio -->
<div class="marquee">
  <span class="fade" style="left:-8px">ORTFOLIO</span>
  <span class="main" style="left:370px">OUR PORTFOLIO</span>
  <span class="fade" style="left:915px">OUR PORTFOLIO</span>
</div>

<div class="photo" style="left:0;top:1703px;width:577px;height:412px;background:linear-gradient(180deg,#b7c3cf 0%,#9aa8b6 40%,#8cc8d4 60%,#6bb6c8 100%)" role="img" aria-label="Infinity-edge rooftop spa pool overlooking a skyline"></div>
<h3 class="project-title" style="left:662px;top:1810px">57th Floor Spa At The<br>Phila Silver Willow</h3>
<div class="plus-link" style="left:662px;top:1912px"><div class="plus"></div>VIEW PROJECT DETAIL</div>

<div class="photo" style="left:621px;top:2115px;width:579px;height:413px;background:linear-gradient(135deg,#3f5f88 0%,#2b6f8d 50%,#1c5c6f 100%)" role="img" aria-label="Swimmer stretching beside an indoor training pool"></div>
<h3 class="project-title" style="left:120px;top:2222px">Aquatic Therapy Portion<br>Of The Phila Ravenhawks<br>Training Facility</h3>
<div class="plus-link" style="left:120px;top:2370px"><div class="plus"></div>VIEW PROJECT DETAIL</div>

<div class="photo" style="left:0;top:2528px;width:577px;height:413px;background:linear-gradient(180deg,#2fb4d8 0%,#1a9fd0 50%,#39b8dc 100%)" role="img" aria-label="Swimmers diving into a competition pool with lane ropes"></div>
<h3 class="project-title" style="left:662px;top:2640px">A 5om Indoor Competition<br>Pool For The Prestigious<br>Dallowmere Academy</h3>
<div class="plus-link" style="left:662px;top:2785px"><div class="plus"></div>VIEW PROJECT DETAIL</div>

<div class="photo" style="left:621px;top:2941px;width:579px;height:412px;background:linear-gradient(180deg,#6d8ba0 0%,#4a97c4 45%,#2f9fd4 100%)" role="img" aria-label="Indoor water park pool with a red slide and swimmers"></div>
<h3 class="project-title" style="left:120px;top:3085px">The Indoor Water Park At<br>The Quenwick Lodge</h3>
<div class="plus-link" style="left:123px;top:3190px"><div class="plus"></div>VIEW PROJECT DETAIL</div>

<!-- cta -->
<div class="cta"></div>
<div class="photo cta-photo" role="img" aria-label="Swimmer climbing a pool ladder"></div>
<h2 class="cta-title"><span class="hl">If you find a high<br>quality contractor</span><br><span class="wh">for your projects?</span></h2>
<div class="btn-blue">CONTACT US</div>

<!-- testimonials -->
<div class="eyebrow" style="left:125px;top:3826px"><svg width="12" height="10" viewBox="0 0 12 10"><path d="M0 0l12 5-12 5 3-5z" fill="#3aa6dd"/></svg>TESTIMONIALS</div>
<h2 class="testi-title">WHAT OUR CLIENT SAY....</h2>
<div class="photo avatar" role="img" aria-label="Client portrait"></div>
<p class="quote">" Lorem Ipsum has been the industry's standard dummy text ever since the 1500s, when an unknown printer took a galley of type and scrambled it to make a type specimen book. It has survived not only Lorem Ipsum has been the industry's standard dummy text ever since the 1500s, when an unknown printer took a galley of type "</p>
<div class="abs" style="left:272px;top:4070px;width:10px;height:2px;background:var(--ink)"></div>
<div class="client" style="left:297px">Client Name</div>
<div class="testi-bar" style="top:3935px;height:16px"></div>
<div class="testi-bar" style="top:3965px;height:16px;background:#c9d6e4;width:1px"></div>
<div class="testi-bar" style="top:3995px;height:16px;background:#c9d6e4;width:1px"></div>

<!-- footer -->
<footer class="footer"></footer>
<div class="footer-line"></div>
<div class="f-brand">
  <div class="brand-dot"></div>
  <div class="brand-name">LARKFIELD<small>AQUATICS · DESIGN | CONSTRUCTION</small></div>
</div>
<p class="f-about">Lorem Ipsum has been the industry's standard dummy text ever since.</p>
<div class="social" style="left:60px"></div>
<div class="social" style="left:105px"></div>

<div class="f-head" style="left:337px">CONTACT US</div>
<svg class="abs" style="left:337px;top:4258px" width="14" height="18" viewBox="0 0 14 18" aria-hidden="true"><path d="M7 0a7 7 0 00-7 7c0 5 7 11 7 11s7-6 7-11a7 7 0 00-7-7zm0 10a3 3 0 110-6 3 3 0 010 6z" fill="#3aa6dd"/></svg>
<div class="f-item" style="left:368px;top:4254px;width:230px"><span class="hl">LARKFIELD AQUATICS</span><br>101 - lorem ipsum simple text print type setting text print</div>
<svg class="abs" style="left:337px;top:4334px" width="16" height="16" viewBox="0 0 24 24" aria-hidden="true"><path d="M6.6 10.8a15 15 0 006.6 6.6l2.2-2.2c.3-.3.7-.4 1-.2 1.1.4 2.3.6 3.6.6.6 0 1 .4 1 1V20c0 .6-.4 1-1 1C10.6 21 3 13.4 3 4c0-.6.4-1 1-1h3.5c.6 0 1 .4 1 1 0 1.3.2 2.5.6 3.6.1.3 0 .7-.2 1z" fill="#3aa6dd"/></svg>
<div class="f-item" style="left:368px;top:4333px">info@larkfieldaquatics.com</div>
<svg class="abs" style="left:337px;top:4368px" width="16" height="12" viewBox="0 0 16 12" aria-hidden="true"><rect width="16" height="12" rx="1" fill="#3aa6dd"/><path d="M0 1l8 6 8-6" stroke="#1b2a55" stroke-width="1.4" fill="none"/></svg>
<div class="f-item" style="left:368px;top:4364px">+(1) 123 456 7890</div>

<div class="f-head" style="left:612px">QUICK LINKS</div>
<ul class="links"><li>Home</li><li>About Us</li><li>Services</li><li>Projects</li><li>Contact Us</li></ul>

<div class="f-head" style="left:888px">NEWSLETTER SIGNUP!</div>
<div class="email-field">Enter Email *</div>
<div class="btn-sub">SUBSCRIBE</div>

<div class="copyright"><span class="hl">©LARKFIELD AQUATICS</span> – 2023 All rights reserved.</div>

</body>
</html>
```